Kelbro TV needs a van wrap Design and logo

Marlo Vestra Wrap Design ( partial wrap or 3/4 full wrap ).. I need a logo too...

I'd will really like if someone can wrap the vestra similar to the kdv within the files.

Target Market(s)

Home Owners

Logo Text

Kelbro TV Installers

Font styles to use
Sans Serif

Colors
ec1f27

Requirements
Must have
• My info 555-219-4086, www.kelbrotv.com, My colors are red white and black .. i will like the best of the best seal as in my old design as outlined with spec below..
• I'm ready to have the wrap installed like asap
Nice to have
• LOGO

```html
<!DOCTYPE html>
<html lang="en">
<head>
<meta charset="utf-8">
<title>Kelbro TV – Van Wrap</title>
<link href="https://fonts.googleapis.com/css2?family=Roboto+Condensed:wght@700&family=Roboto:wght@500;700&display=swap" rel="stylesheet">
<style>
  :root {
    --brand-red: #ec1f27;
    --deep-red: #c8161d;
    --ink: #111111;
    --paper: #ffffff;
    --seal-gold: #d9a61e;
  }
  html, body { margin: 0; padding: 0; overflow: hidden; background: var(--paper); }
  .canvas { width: 1200px; height: 790px; position: relative; overflow: hidden; }
  .canvas svg { display: block; width: 1200px; height: 790px; }
  .phone { font-family: "Roboto Condensed", "Arial Narrow", sans-serif; font-weight: 700; fill: var(--brand-red); font-size: 70px; }
  .tagline { font-family: "Roboto", Arial, sans-serif; font-weight: 500; fill: var(--ink); font-size: 24px; }
  .services { font-family: "Roboto", Arial, sans-serif; font-weight: 700; fill: var(--paper); font-size: 15px; }
  .brand-name { font-family: "Roboto", Arial, sans-serif; font-weight: 700; fill: var(--ink); font-size: 46px; letter-spacing: -1px; }
  .web { font-family: "Roboto", Arial, sans-serif; font-weight: 700; fill: var(--paper); font-size: 26px; }
</style>
</head>
<body>
<div class="canvas">
<svg viewBox="0 0 1500 988" xmlns="http://www.w3.org/2000/svg">
  <defs>
    <clipPath id="van-body-clip">
      <path d="M80,350 L84,300 Q100,272 160,258 L225,205 Q300,120 380,78 Q425,58 490,55 L1380,36 Q1402,38 1406,62 L1414,200 L1408,350 L1330,352 Q1312,306 1262,304 Q1208,304 1188,352 L1060,362 L290,384 Q272,335 222,334 Q168,334 150,372 L84,370 Z"/>
    </clipPath>
    <linearGradient id="gear-fill" x1="0" y1="0" x2="0" y2="1">
      <stop offset="0" stop-color="#3a3d44"/>
      <stop offset="1" stop-color="#8a8d94"/>
    </linearGradient>

    <g id="van-side">
      <g clip-path="url(#van-body-clip)">
        <rect x="60" y="20" width="1380" height="380" fill="var(--paper)"/>
        <path class="front-sweep" d="M60,400 L60,250 L220,170 Q320,90 430,60 L560,45 L520,62 Q400,80 300,160 L250,215 L230,300 L200,400 Z" fill="var(--brand-red)"/>
        <path d="M180,400 L250,270 L268,270 L200,400 Z" fill="var(--ink)"/>
        <path d="M205,400 L272,270 L285,270 L220,400 Z" fill="var(--paper)"/>
        <path d="M440,80 L545,48 L560,46 L450,84 Z" fill="var(--ink)"/>
        <path class="rear-panel" d="M690,400 L1070,20 L1440,20 L1440,400 Z" fill="var(--brand-red)"/>
        <line class="service-band" x1="690" y1="400" x2="1080" y2="10" stroke="var(--ink)" stroke-width="28"/>
        <line x1="980" y1="380" x2="1110" y2="300" stroke="var(--ink)" stroke-width="12"/>
        <line x1="1000" y1="386" x2="1120" y2="312" stroke="var(--paper)" stroke-width="6"/>
        <path class="window" d="M245,190 Q300,130 360,100 Q420,88 478,90 Q486,150 480,215 Q470,240 400,250 L210,278 Q200,250 245,190 Z" fill="var(--paper)" stroke="var(--deep-red)" stroke-width="1.5"/>
        <rect x="1030" y="40" width="340" height="300" fill="url(#gear-fill)" opacity="0.9"/>
        <circle cx="998" cy="258" r="48" fill="var(--seal-gold)"/>
      </g>
      <path d="M80,350 L84,300 Q100,272 160,258 L225,205 Q300,120 380,78 Q425,58 490,55 L1380,36 Q1402,38 1406,62 L1414,200 L1408,350 L1330,352 Q1312,306 1262,304 Q1208,304 1188,352 L1060,362 L290,384 Q272,335 222,334 Q168,334 150,372 L84,370 Z" fill="none" stroke="var(--deep-red)" stroke-width="1.2"/>
    </g>

    <g id="web-strip">
      <path d="M342,436 L1013,425 L1006,455 L350,462 Z" fill="var(--paper)" stroke="var(--deep-red)" stroke-width="1.2"/>
      <path d="M560,433 L1013,425 L1006,455 L540,460 Z" fill="var(--brand-red)"/>
      <path d="M470,460 L540,434 L560,433 L490,460 Z" fill="var(--ink)"/>
      <path d="M925,456 L945,428 L955,428 L935,456 Z" fill="var(--ink)"/>
      <path d="M945,456 L965,428 L975,428 L955,456 Z" fill="var(--paper)"/>
    </g>
  </defs>

  <g class="van-left">
    <use href="#van-side"/>
    <g role="img" aria-label="Home theater equipment: flat-screen TV, tower speakers and media console">
      <rect x="1030" y="40" width="340" height="300" fill="none"/>
    </g>
    <text class="phone" x="535" y="128" textLength="395" lengthAdjust="spacingAndGlyphs">555.219.4086</text>
    <text class="tagline" x="563" y="157" textLength="335" lengthAdjust="spacingAndGlyphs">We Hang TVs &amp; Hide the Wires</text>
    <text class="services" transform="translate(724,376) rotate(-45)" textLength="440" lengthAdjust="spacingAndGlyphs">Audio ● Video ● Home Theater ● HD Antennas ● TV Installations</text>
    <text class="brand-name" x="248" y="338">Kelbro TV</text>
    <use href="#web-strip"/>
    <text class="web" x="596" y="454">www.KelbroTV.com</text>
  </g>

  <g class="van-right">
    <use href="#van-side" transform="translate(1500,488) scale(-1,1)"/>
    <g role="img" aria-label="Home theater equipment: flat-screen TV, tower speakers and media console">
      <rect x="130" y="528" width="340" height="300" fill="none"/>
    </g>
    <text class="phone" x="565" y="618" textLength="395" lengthAdjust="spacingAndGlyphs">555.219.4086</text>
    <text class="tagline" x="600" y="645" textLength="355" lengthAdjust="spacingAndGlyphs">We Hang TVs &amp; Hide the Wires</text>
    <text class="services" transform="translate(462,550) rotate(45)" textLength="440" lengthAdjust="spacingAndGlyphs">Audio ● Video ● Home Theater ● HD Antennas ● TV Installations</text>
    <text class="brand-name" x="1006" y="822">Kelbro TV</text>
    <use href="#web-strip" transform="translate(1500,487) scale(-1,1)"/>
    <text class="web" x="607" y="941">www.KelbroTV.com</text>
  </g>
</svg>
</div>
</body>
</html>
```